Product label for herbal salves, lotions, soaps and tinctures

We need a very simple, clean and organic looking label that can be used for an ointment jar, a lotion bottle and a dropper bottle.
We have an existing logo (see attached). We like the colors white, olive green, gold and black. It needs to include product name as dominant and logo. It also needs to include an ingredient list, and usage statement. Include weight of product, distributed by, made in the USA, and QVX statement.
Example of what needs to be present:
Logo
Name: Tranquil Ease Blend
Used for: For Muscle Aches, Arthritis, Tendonitis, Headaches
To Use: For muscle aches, arthritis and tendonitis, massage into affected area. For tension headache apply to neck, temples and forehead.
Store in a cool and dry place, away from direct heat and sunlight.
Weight of product: 1.75
DIST. BY: Copper Brook Herbal
Made in the USA
This product is not intended to diagnose, treat, cure
or prevent any disease. Not regulated
by the QVX. Please consult your health care practitioner
before using product. Discontinue use if any adverse reaction occurs.
Ingredient list:
Wildcrafted Ingredients:
Ashwagandha Root, Peppermint Leaf, Hops Flowers, St. John’s Wort Herb, Arnica Flowers, Green Tea Leaf, Alfalfa Leaf, Dandelion Root, Burdock Root, Chickweed Herb, Chaparral Leaf, Yarrow Flowers, Boneset Herb, Moringa Leaf, Meadowsweet Herb, Nettle Leaf
Organic Ingredients:
Olive Oil, Aloe Leaf, Sweet Birch Bark, Helichrysum Flowers, Holy Basil Leaf, Borage Herb, Ginger Root, Angelica Root, White Willow Bark, Mustard Seed, Beeswax, Vitamin E, Essential Oils
Dimensions of Jar:
Circumference: 7 in.
Height: 1 in.

```html
<!DOCTYPE html>
<html lang="en">
<head>
<meta charset="utf-8">
<title>Tranquil Ease Blend – Jar Label</title>
<link rel="stylesheet" href="https://fonts.googleapis.com/css2?family=Oswald:wght@500&family=Playfair+Display:wght@700&family=Archivo+Narrow:wght@400;700&display=swap">
<style>
  :root {
    --page-bg: #e4e4e4;
    --label-bg: #ffffff;
    --ink: #141414;
    --olive: #6b7327;
    --gold: #c79a2e;
    --body-text: #222222;
  }
  * { margin: 0; padding: 0; box-sizing: border-box; }
  html, body { width: 1200px; height: 1200px; overflow: hidden; }
  body {
    background: var(--page-bg);
    position: relative;
    font-family: "Archivo Narrow", "Arial Narrow", sans-serif;
    color: var(--body-text);
  }
  .label {
    position: absolute;
    left: 65px;
    top: 522px;
    width: 1070px;
    height: 155px;
    background: var(--label-bg);
    box-shadow: 4px 5px 8px rgba(0,0,0,0.35);
  }
  .ingredients {
    position: absolute;
    left: 23px;
    top: 18px;
    width: 230px;
    font-size: 7px;
    line-height: 1.3;
  }
  .ingredients h3 { font-size: 7px; font-weight: 700; }
  .ingredients p + h3 { margin-top: 7px; }

  .brand {
    position: absolute;
    left: 0;
    width: 1070px;
    top: 24px;
    text-align: center;
    font-family: "Playfair Display", Georgia, serif;
    font-weight: 700;
    font-size: 19px;
    color: var(--olive);
    letter-spacing: 0.2px;
  }
  .product-name {
    position: absolute;
    left: 0;
    width: 1070px;
    top: 56px;
    text-align: center;
    font-family: "Oswald", "Arial Narrow", sans-serif;
    font-weight: 500;
    font-size: 38px;
    line-height: 1.1;
    color: var(--ink);
    letter-spacing: 1px;
    text-transform: uppercase;
  }
  .divider {
    position: absolute;
    left: 363px;
    top: 111px;
    width: 357px;
    height: 1.5px;
    background: var(--gold);
  }
  .uses {
    position: absolute;
    left: 0;
    width: 1070px;
    top: 121px;
    text-align: center;
    font-family: "Playfair Display", Georgia, serif;
    font-weight: 700;
    font-size: 13px;
    color: var(--ink);
  }
  .directions {
    position: absolute;
    left: 832px;
    top: 16px;
    width: 228px;
    font-size: 7px;
    line-height: 1.3;
  }
  .directions p + p { margin-top: 5px; }
  .directions strong { font-weight: 700; }
  .caution {
    position: absolute;
    left: 832px;
    top: 82px;
    width: 226px;
    height: 23px;
    background: var(--olive);
    color: #ffffff;
    font-size: 7px;
    font-weight: 700;
    line-height: 1.25;
    padding: 3px 11px;
  }
  .distribution {
    position: absolute;
    left: 832px;
    top: 115px;
    width: 226px;
    font-size: 7px;
    line-height: 1.3;
  }
  .dist-brand {
    font-family: "Archivo Narrow", "Arial Narrow", sans-serif;
    font-weight: 700;
    color: var(--olive);
    margin-left: 3px;
  }
  .weight {
    position: absolute;
    right: 0;
    bottom: 0;
  }
</style>
</head>
<body>
  <section class="label" aria-label="Tranquil Ease Blend jar label">
    <div class="ingredients">
      <h3>Wildcrafted Ingredients:</h3>
      <p>Ashwagandha Root, Peppermint Leaf, Hops Flowers, St. John’s Wort Herb, Arnica Flowers, Green Tea Leaf, Alfalfa Leaf, Dandelion Root, Burdock Root, Chickweed Herb, Chaparral Leaf, Yarrow Flowers, Boneset Herb, Moringa Leaf, Meadowsweet Herb, Nettle Leaf</p>
      <h3>Organic Ingredients:</h3>
      <p>Olive Oil, Aloe Leaf, Sweet Birch Bark, Helichrysum Flowers, Holy Basil Leaf, Borage Herb, Ginger Root, Angelica Root, White Willow Bark, Mustard Seed, Beeswax, Vitamin E, Essential Oils</p>
    </div>

    <div class="brand">Copper Brook Herbal</div>
    <h1 class="product-name">Tranquil Ease Blend</h1>
    <div class="divider"></div>
    <p class="uses">For Muscle Aches, Arthritis, Tendonitis, Headaches</p>

    <div class="directions">
      <p><strong>To Use:</strong> For muscle aches, arthritis and tendonitis, massage into affected area. For tension headache apply to neck, temples and forehead. Store in a cool and dry place, away from direct heat and sunlight.</p>
      <p>This product is not intended to diagnose, treat, cure or prevent any disease. Not regulated by the QVX.</p>
    </div>
    <div class="caution">Please consult your health care practitioner before using product. Discontinue use if any adverse reaction occurs.</div>
    <div class="distribution">
      <p>DIST. BY: <span class="dist-brand">Copper Brook Herbal</span></p>
      <p>Made in the USA</p>
      <p class="weight">Weight: 1.75</p>
    </div>
  </section>
</body>
</html>
```